Professional violinist needs business cards

I am trying to attract the following jobs:
-private violin lessons (primarily classical)
-performance gigs (weddings, birthday parties, funerals, etc.)
-collaborations with other artists (studio recordings, performances)

I want to communicate that I have a very high standard of excellence for my work, but I also love people and celebrations.
Values/style words I like are:
love, joy, peace, fun, beauty, authenticity, excellence, warmth, refined/sleek, free spirited. If that's too confusing, just ignore :)

I will attach my favorite business card template that I could find on Canva. The lines are supposed to be like a music staff, which I think is really cool, but I also don't want it to look too busy. I like the simple black and white--I think it looks sharp--but I also am open to other ideas. I also have seen business cards with pictures included that looked great, so I attached an image that could be used as well.

I am also attaching a file that I made of my initials that could be used as a logo, but I'm not sure if it should be included.

Information on the card:
-My name (18 letters total)
-"violinist"
-phone number, email, website

Thank you!

```html
<!DOCTYPE html>
<html lang="en">
<head>
<meta charset="UTF-8">
<title>Marianne Holloway — Violinist Business Cards</title>
<link rel="stylesheet" href="https://fonts.googleapis.com/css2?family=Dancing+Script:wght@600&family=Cinzel:wght@400&family=Quattrocento:wght@400&display=swap">
<style>
  :root {
    --backdrop: #1a1b1c;
    --card-dark: #23272a;
    --photo-stone: #6f6554;
    --photo-stone-light: #8a806c;
    --photo-shadow: #1c1d1f;
    --ink-white: #f4f2ee;
    --ink-soft: #d9d6cf;
    --gold: #cdbb94;
    --staff-line: rgba(255, 255, 255, 0.18);
  }
  * { box-sizing: border-box; margin: 0; padding: 0; }
  html, body {
    width: 1200px;
    height: 1108px;
    overflow: hidden;
    background: var(--backdrop);
  }
  .canvas {
    position: relative;
    width: 1200px;
    height: 1108px;
    display: flex;
    justify-content: center;
    align-items: center;
    gap: 70px;
  }
  .card {
    position: relative;
    width: 440px;
    height: 690px;
    border-radius: 42px;
    overflow: hidden;
    box-shadow: 0 18px 40px rgba(0, 0, 0, 0.55);
  }

  /* Monogram stand-in: initials in the text font with one plain circle */
  .monogram {
    display: inline-flex;
    align-items: center;
    gap: 10px;
    font-family: "Cinzel", serif;
    font-weight: 400;
    font-size: 44px;
    line-height: 1;
    letter-spacing: 2px;
    color: var(--ink-white);
  }
  .monogram__dot {
    width: 10px;
    height: 10px;
    border-radius: 50%;
    background: currentColor;
  }

  .name {
    font-family: "Dancing Script", cursive;
    font-weight: 600;
    font-size: 50px;
    line-height: 1.1;
    color: var(--ink-white);
  }
  .role {
    display: flex;
    align-items: center;
    justify-content: center;
    gap: 22px;
    margin-top: 8px;
    font-family: "Cinzel", serif;
    font-size: 19px;
    letter-spacing: 5px;
    color: var(--ink-white);
  }
  .role__rule {
    width: 72px;
    height: 2px;
    background: var(--ink-white);
  }

  /* Front */
  .card--front { background: var(--photo-shadow); }
  .card__photo {
    position: absolute;
    inset: 0;
    background:
      linear-gradient(180deg, rgba(0,0,0,0) 40%, rgba(20,21,23,0.85) 75%, var(--photo-shadow) 100%),
      linear-gradient(160deg, var(--photo-stone-light) 0%, var(--photo-stone) 55%, #4a443a 100%);
  }
  .card--front .card__brand {
    position: absolute;
    left: 0; right: 0;
    top: 440px;
    text-align: center;
  }
  .card--front .monogram { margin-bottom: 18px; }

  /* Back */
  .card--back { background: var(--card-dark); }
  .staff {
    position: absolute;
    left: 0;
    top: 150px;
    width: 440px;
    height: 110px;
  }
  .card--back .card__brand {
    position: absolute;
    left: 0; right: 0;
    top: 175px;
    text-align: center;
  }
  .card--back .monogram { color: var(--gold); margin-bottom: 52px; }
  .contact {
    position: absolute;
    left: 0; right: 0;
    top: 430px;
    text-align: center;
    font-family: "Quattrocento", serif;
    font-style: normal;
    font-size: 19px;
    line-height: 1.55;
    color: var(--ink-soft);
  }
  .contact__highlight { color: var(--gold); }
  .contact__city { margin-top: 14px; }
</style>
</head>
<body>
  <main class="canvas">
    <section class="card card--front">
      <div class="card__photo" role="img" aria-label="Portrait photo of the violinist in a black gown holding her violin and bow on stone steps beside a stone wall"></div>
      <div class="card__brand">
        <div class="monogram">MH<span class="monogram__dot"></span></div>
        <div class="name">Marianne Holloway</div>
        <div class="role"><span class="role__rule"></span>Violinist<span class="role__rule"></span></div>
      </div>
    </section>

    <section class="card card--back">
      <svg class="staff" viewBox="0 0 440 110" aria-hidden="true">
        <g stroke="rgba(255,255,255,0.18)" stroke-width="1.2">
          <line x1="0" y1="10" x2="440" y2="10"/>
          <line x1="0" y1="32" x2="440" y2="32"/>
          <line x1="0" y1="54" x2="440" y2="54"/>
          <line x1="0" y1="76" x2="440" y2="76"/>
          <line x1="0" y1="98" x2="440" y2="98"/>
        </g>
      </svg>
      <div class="card__brand">
        <div class="monogram">MH<span class="monogram__dot"></span></div>
        <div class="name">Marianne Holloway</div>
        <div class="role">Violinist</div>
      </div>
      <address class="contact">
        <div>+1 (555) 214-3087</div>
        <div>Marianne@MarianneHolloway.com</div>
        <div>www.<span class="contact__highlight">MarianneHolloway</span>.com</div>
        <div class="contact__city">Annapolis, MD</div>
      </address>
    </section>
  </main>
</body>
</html>
```